Create a Stalvik-looking dashboard for our Open Compass Speedometer that can look similar to my AI-generated dashboard attached, but with: 1) clear borders on all four sides, 2) is created in a way that we can modify the numbers weekly, say maybe you create the graphic that we can inset the excel spreadsheet numbers into, but ideally mixed with the Stalvik look black leather bubble design shown in the dashboard?; 3) uses the exact numbers shown in the attachment; 4) the speedometer on top should have four equal colors of red on left (-1), then yellow (0), then light green (1), then medium green (2); 5) the gauge on the top left should be the graphic that includes 0-100% bar that is currently 33%, and right below that a -20 to +20 bar with the arrow pointing to 11.9%, with color coding similar to the graphic; 6) replace the Stalvik logo in the middle with a similar shaped shield with blue background with the "T" logo with the eagle inside it, like attached

```html
<!DOCTYPE html>
<html lang="en">
<head>
<meta charset="utf-8">
<title>Open Compass Speedometer</title>
<link href="https://fonts.googleapis.com/css2?family=Cinzel:wght@700;900&family=Oswald:wght@500;600;700&family=Roboto:wght@400;500&display=swap" rel="stylesheet">
<style>
  :root{
    --page:#ffffff;
    --leather-hi:#d8222c;
    --leather:#a8121c;
    --leather-dark:#5a070d;
    --carbon:#1c1c1e;
    --chrome:#c9c9cc;
    --gold:#f0b83a;
    --gold-dark:#a8701a;
    --band-red:#d42a1e;
    --band-yellow:#e6c414;
    --band-lightgreen:#7cd63a;
    --band-green:#2a9e2a;
    --row-bull:#35e234;
    --row-bulish:#2fe6b4;
    --row-bearish:#e8da0c;
    --row-bear:#f04a4c;
    --cell-text:#111111;
    --teal:#3fe0b8;
    --sheet-line:#e1e3e6;
    --sheet-text:#202124;
    --sheet-muted:#5f6368;
  }
  *{box-sizing:border-box;margin:0;padding:0}
  html,body{width:1200px;height:800px;overflow:hidden;background:var(--page)}
  .canvas{position:relative;width:1200px;height:800px}

  .dashboard{
    position:absolute;left:117px;top:46px;width:944px;height:572px;
    overflow:hidden;box-shadow:0 14px 30px rgba(0,0,0,.55);
  }
  .dashboard-backdrop{
    position:absolute;inset:0;
    background:
      radial-gradient(ellipse 60% 40% at 50% 8%, var(--leather-hi), transparent 70%),
      radial-gradient(ellipse 30% 45% at 8% 70%, var(--leather-hi), transparent 70%),
      radial-gradient(ellipse 30% 45% at 92% 70%, var(--leather-hi), transparent 70%),
      linear-gradient(180deg,#202022 0%,#202022 8%,var(--leather) 14%,var(--leather-dark) 100%);
  }
  .dashboard-art{position:absolute;inset:0}

  .gauge-title{
    position:absolute;left:0;width:944px;top:230px;text-align:center;
    font-family:"Cinzel",serif;font-weight:900;font-size:21px;line-height:28px;letter-spacing:.5px;
    color:var(--gold);text-shadow:0 2px 2px #000;
  }
  .gauge-readout{
    position:absolute;width:110px;text-align:center;font-family:"Oswald",sans-serif;font-weight:600;
    color:#e9e9ea;text-shadow:0 2px 3px #000;line-height:30px;
  }
  .readout-left{left:148px;top:196px;font-size:23px}
  .readout-right{left:692px;top:198px;font-size:21px}

  .trend-head{
    position:absolute;left:171px;top:280px;width:615px;display:grid;
    grid-template-columns:204px 182px 229px;
  }
  .trend-head span{
    text-align:center;font-family:"Oswald",sans-serif;font-weight:600;font-size:16px;line-height:22px;
    color:var(--gold);text-shadow:0 2px 2px #000;
  }
  .trend-row{position:absolute;height:34.4px;display:grid}
  .trend-row span{
    display:flex;align-items:center;justify-content:center;
    font-family:"Oswald",sans-serif;font-weight:600;font-size:14px;color:var(--cell-text);
    border-right:1px dashed rgba(0,0,0,.55);
  }
  .trend-row span:first-child{justify-content:flex-start}
  .trend-row span:last-child{border-right:none}
  .row-bull{left:171px;top:310px;grid-template-columns:204px 182px 229px;background:var(--row-bull)}
  .row-bull span:first-child{padding-left:39px}
  .row-bulish{left:183px;top:344.4px;grid-template-columns:192px 182px 213px;background:var(--row-bulish)}
  .row-bulish span:first-child{padding-left:27px}
  .row-bearish{left:187px;top:378.8px;grid-template-columns:188px 182px 206px;background:var(--row-bearish)}
  .row-bearish span:first-child{padding-left:23px}
  .row-bear{left:190px;top:413.2px;grid-template-columns:185px 182px 200px;background:var(--row-bear);border-radius:0 0 10px 10px}
  .row-bear span:first-child{padding-left:20px}

  .start-button{
    position:absolute;left:89px;top:408px;width:60px;height:60px;border-radius:50%;
    background:radial-gradient(circle at 40% 35%,#e02a2a,#7a0a0a);
    border:3px solid var(--chrome);box-shadow:0 3px 6px #000;
    display:flex;flex-direction:column;align-items:center;justify-content:center;
    font-family:"Roboto",sans-serif;font-weight:500;font-size:8.5px;line-height:1.15;color:#fff;text-align:center;
  }

  .sheet{
    position:absolute;left:413px;top:619px;width:352px;height:170px;background:#fff;
    font-family:"Roboto",sans-serif;color:var(--sheet-text);overflow:hidden;
  }
  .sheet-title{display:flex;align-items:center;gap:8px;padding:6px 10px 0}
  .sheet-icon{width:14px;height:18px;background:#1fa463;border-radius:2px}
  .sheet-name{font-size:11px}
  .sheet-menu{padding:2px 0 0 34px;font-size:8px;color:var(--sheet-text);word-spacing:5px}
  .sheet-toolbar{margin:8px 8px 0;height:18px;border-radius:9px;background:#edf2fa;font-size:8px;color:var(--sheet-muted);padding:4px 12px}
  .sheet-formula{margin-top:6px;height:16px;border-bottom:1px solid var(--sheet-line);font-size:7px;padding:3px 6px;color:var(--sheet-muted)}
  .sheet-grid{display:grid;grid-template-columns:26px 115px 75px 100px 36px;font-size:7px}
  .sheet-grid div{border-right:1px solid var(--sheet-line);border-bottom:1px solid var(--sheet-line);padding:2px 2px;line-height:1.35}
  .sheet-grid .col-head{background:#f8f9fa;text-align:center;color:var(--sheet-muted)}
  .sheet-grid .row-num{background:#f8f9fa;text-align:center;color:var(--sheet-muted)}
</style>
</head>
<body>
<div class="canvas">
  <section class="dashboard">
    <div class="dashboard-backdrop" role="img" aria-label="Red stitched leather and carbon fibre car dashboard interior"></div>

    <svg class="dashboard-art" width="944" height="572" viewBox="0 0 944 572">
      <defs>
        <radialGradient id="hubGradient" cx=".4" cy=".35" r=".7">
          <stop offset="0" stop-color="#ffe08a"/>
          <stop offset="1" stop-color="#b07a12"/>
        </radialGradient>
      </defs>

      <!-- carbon instrument panel -->
      <path d="M70 150 Q120 110 250 110 L320 110 Q380 40 477 36 Q574 40 634 110 L720 110 Q840 110 880 160 L890 380 Q880 490 780 500 L170 500 Q70 490 60 380 Z" fill="var(--carbon)" stroke="#000" stroke-width="3"/>

      <!-- main speedometer: four equal bands -->
      <g class="main-gauge">
        <path d="M317 210 A160 160 0 0 1 637 210" fill="none" stroke="var(--chrome)" stroke-width="10"/>
        <path d="M477 210 L329 210 A148 148 0 0 1 372.3 105.3 Z" fill="var(--band-red)"/>
        <path d="M477 210 L372.3 105.3 A148 148 0 0 1 477 62 Z" fill="var(--band-yellow)"/>
        <path d="M477 210 L477 62 A148 148 0 0 1 581.7 105.3 Z" fill="var(--band-lightgreen)"/>
        <path d="M477 210 L581.7 105.3 A148 148 0 0 1 625 210 Z" fill="var(--band-green)"/>
        <path d="M341 210 A136 136 0 0 1 613 210" fill="none" stroke="#fff4c8" stroke-width="8" stroke-dasharray="1.5 6" opacity=".75"/>
        <g font-family="Oswald, sans-serif" font-weight="700" font-size="30" fill="#f4c04a" stroke="#3a2400" stroke-width="1" text-anchor="middle">
          <text x="368" y="202">-1</text>
          <text x="420" y="124">0</text>
          <text x="522" y="122">1</text>
          <text x="586" y="202">2</text>
        </g>
        <path d="M425 210 A52 52 0 0 1 529 210 Z" fill="#1a1a1a" stroke="var(--chrome)" stroke-width="3"/>
        <polygon points="471,202 483,212 549,118" fill="var(--gold)" stroke="var(--gold-dark)" stroke-width="1"/>
        <circle cx="477" cy="206" r="14" fill="url(#hubGradient)" stroke="#333" stroke-width="2"/>
      </g>

      <!-- left percent gauge -->
      <g class="percent-gauge">
        <circle cx="203" cy="210" r="82" fill="#2a2a2c" stroke="var(--chrome)" stroke-width="5"/>
        <circle cx="203" cy="210" r="70" fill="#222"/>
        <circle cx="203" cy="210" r="60" fill="none" stroke="#0f3a34" stroke-width="8" pathLength="100" stroke-dasharray="75 25" transform="rotate(135 203 210)"/>
        <circle cx="203" cy="210" r="60" fill="none" stroke="var(--teal)" stroke-width="8" pathLength="100" stroke-dasharray="24.75 75.25" transform="rotate(210 203 210)"/>
      </g>

      <!-- right change gauge -->
      <g class="change-gauge">
        <circle cx="747" cy="210" r="84" fill="#2a2a2c" stroke="var(--chrome)" stroke-width="5"/>
        <circle cx="747" cy="210" r="52" fill="#222"/>
        <circle cx="747" cy="210" r="62" fill="none" stroke="#2ed03a" stroke-width="9" pathLength="360" stroke-dasharray="80 280" transform="rotate(170 747 210)"/>
        <circle cx="747" cy="210" r="62" fill="none" stroke="#f2e21a" stroke-width="9" pathLength="360" stroke-dasharray="70 290" transform="rotate(250 747 210)"/>
        <circle cx="747" cy="210" r="62" fill="none" stroke="#e8321e" stroke-width="9" pathLength="360" stroke-dasharray="70 290" transform="rotate(320 747 210)"/>
        <polygon points="744,148 750,148 747,166" fill="#111" stroke="#ffd23a" stroke-width="1.5"/>
        <g font-family="Oswald, sans-serif" font-weight="600" font-size="10" fill="var(--gold)" text-anchor="middle">
          <text x="762" y="152">0</text>
          <text x="697" y="173">10</text>
          <text x="674" y="219">20</text>
          <text x="814" y="205">-10</text>
          <text x="805" y="262">-20</text>
        </g>
      </g>

      <!-- indicator lights -->
      <circle cx="276" cy="130" r="5" fill="#ff3030"/>
      <circle cx="675" cy="130" r="5" fill="#ff3030"/>

      <!-- title banner -->
      <path d="M232 262 L296 228 L658 228 L722 262 Z" fill="#151517" stroke="var(--chrome)" stroke-width="1.5"/>
    </svg>

    <div class="gauge-readout readout-left">33%</div>
    <div class="gauge-readout readout-right">11.9%</div>
    <div class="gauge-title">OPEN COMPASS SPEEDOMETER</div>

    <div class="trend-head"><span>GEAR</span><span>CURRENT TREND</span><span>LAST TREND CHANGE</span></div>
    <div class="trend-row row-bull"><span>2 TURBO BOOST</span><span>BULL</span><span>FRIDAY, AUGUST 15,</span></div>
    <div class="trend-row row-bulish"><span>1 ACCELERATOR PEDAL</span><span>BULISH</span><span>2025</span></div>
    <div class="trend-row row-bearish"><span>0 BRAKES</span><span>BEARISH</span><span>-</span></div>
    <div class="trend-row row-bear"><span>-1 REVERSE</span><span>BEAR</span><span>-</span></div>

    <div class="start-button"><span>ENGINE</span><span>START</span></div>
  </section>

  <section class="sheet">
    <div class="sheet-title"><span class="sheet-icon"></span><span class="sheet-name">Open Compass Speedometer</span></div>
    <div class="sheet-menu">File Edit View Insert Format Data Tools Extensions Help</div>
    <div class="sheet-toolbar">Menus &nbsp; 100% &nbsp; $ &nbsp; % &nbsp; 123 &nbsp; Default</div>
    <div class="sheet-formula">H25 &nbsp; fx</div>
    <div class="sheet-grid">
      <div class="col-head"></div><div class="col-head">A</div><div class="col-head">B</div><div class="col-head">C</div><div class="col-head"></div>
      <div class="row-num">1</div><div>Gear</div><div>Trend</div><div>TrendChange</div><div></div>
      <div class="row-num">2</div>
      <div>2 TURBO BOOST<br>1 ACCELERATOR PEDAL<br>0 BRAKES<br>-1 REVERSE</div>
      <div>BULL<br>BULISH<br>BEARISH<br>BEAR</div>
      <div>Friday, August 15, 2025<br>-<br>-<br>-</div><div></div>
      <div class="row-num">3</div><div></div><div></div><div></div><div></div>
    </div>
  </section>
</div>
</body>
</html>
```